Looking for a cool & simple business-card-design for digital agency

Hi!

We are a web agency that offers Reputation Management, Vextor & Seo Services and software development. We like cool things, we like innovative styles.

We have uploaded our logo.

Project Deadline Extended Reason: Client does not want any designs with the colorful logo. Please send us submissions ONLY with the blac and white logo. What the client would like to see:1) Back of the card: is a silver logo on a black background2) front of the card with all the data, please use white background and black logo thank you Added Friday, May 8, 2015

Industry/Entity Type

Software

```html
<!DOCTYPE html>
<html lang="en">
<head>
<meta charset="utf-8">
<title>Nexora Business Card</title>
<link href="https://fonts.googleapis.com/css2?family=Open+Sans:wght@400;600;700&display=swap" rel="stylesheet">
<style>
  :root {
    --backdrop: #d9d9d9;
    --card-black: #0e0e0e;
    --card-black-soft: #262626;
    --card-white: #ffffff;
    --card-white-soft: #f1f1f1;
    --silver: #e4e4e4;
    --silver-dark: #9a9a9a;
    --ink: #111111;
    --ink-muted: #555555;
    --text-muted: #bdbdbd;
    --divider: #c4c4c4;
  }
  * { margin: 0; padding: 0; box-sizing: border-box; }
  html, body {
    width: 1200px; height: 852px; overflow: hidden;
    background: var(--backdrop);
    font-family: "Open Sans", Arial, sans-serif;
  }
  .stage {
    position: relative; width: 1200px; height: 852px;
    display: flex; align-items: center; justify-content: center; gap: 60px;
  }
  .card {
    position: relative; width: 520px; height: 298px;
    border-radius: 12px; overflow: hidden;
    box-shadow: 0 10px 24px rgba(0,0,0,0.25);
  }

  /* Logo side: silver on black */
  .card--brand {
    display: flex; align-items: center; justify-content: center;
    background: linear-gradient(135deg, var(--card-black-soft) 0%, var(--card-black) 55%, #1a1a1a 100%);
  }
  .brand-lockup { display: flex; flex-direction: column; align-items: center; gap: 6px; }
  .brand-lockup__row { display: flex; align-items: center; gap: 14px; }
  .brand-lockup__square { width: 26px; height: 26px; background: var(--silver); }
  .brand-lockup__name {
    font-size: 52px; font-weight: 700; color: var(--silver);
    letter-spacing: 1px; line-height: 1;
  }
  .brand-lockup__tagline {
    font-size: 15px; font-weight: 400; color: var(--text-muted);
    letter-spacing: 6px; text-transform: uppercase;
  }

  /* Details side: black logo on white */
  .card--details {
    display: flex;
    background: linear-gradient(135deg, var(--card-white) 0%, var(--card-white-soft) 100%);
  }
  .card--details .silver-band {
    position: absolute; left: 0; right: 0; bottom: 0; height: 18px;
    background: linear-gradient(180deg, var(--silver) 0%, var(--silver-dark) 100%);
  }
  .details-brand {
    width: 220px; display: flex; align-items: center; justify-content: center;
    gap: 10px; padding-bottom: 18px;
  }
  .details-brand__square { width: 20px; height: 20px; background: var(--ink); }
  .details-brand__name { font-size: 34px; font-weight: 700; color: var(--ink); line-height: 1; }
  .details-divider {
    width: 1px; background: var(--divider);
    margin: 40px 0 58px;
  }
  .details-info {
    flex: 1; padding: 44px 20px 0 22px; color: var(--ink);
  }
  .person__name { font-size: 19px; font-weight: 700; line-height: 1.3; }
  .person__role { font-size: 11px; color: var(--ink-muted); margin-top: 1px; }
  .contact-list { list-style: none; margin-top: 52px; }
  .contact-list li {
    display: flex; align-items: center; gap: 8px;
    font-size: 13px; line-height: 1.55; white-space: nowrap;
  }
  .contact-list svg { width: 11px; height: 11px; flex: none; fill: var(--ink); }
  .contact-list .fax { display: inline-flex; align-items: center; gap: 5px; margin-left: 6px; }
</style>
</head>
<body>
<main class="stage">
  <section class="card card--brand" aria-label="Card back">
    <div class="brand-lockup">
      <div class="brand-lockup__row">
        <span class="brand-lockup__square"></span>
        <span class="brand-lockup__name">Nexora</span>
      </div>
      <span class="brand-lockup__tagline">Digitale Strategien</span>
    </div>
  </section>

  <section class="card card--details" aria-label="Card front">
    <div class="details-brand">
      <span class="details-brand__square"></span>
      <span class="details-brand__name">Nexora</span>
    </div>
    <div class="details-divider"></div>
    <div class="details-info">
      <p class="person__name">Your Long Name</p>
      <p class="person__role">Managing Director</p>
      <ul class="contact-list">
        <li>
          <svg viewBox="0 0 12 12"><path d="M6 0a4 4 0 0 0-4 4c0 3 4 8 4 8s4-5 4-8a4 4 0 0 0-4-4zm0 5.5A1.5 1.5 0 1 1 6 2.5a1.5 1.5 0 0 1 0 3z"/></svg>
          Your Commercial or office address
        </li>
        <li>
          <svg viewBox="0 0 12 12"><path d="M2.5 0.5l2 2.5-1 1.5a7 7 0 0 0 4 4l1.5-1 2.5 2-1.5 2C4 11 1 8 0.5 2z"/></svg>
          00.00.00.0000
          <span class="fax">
            <svg viewBox="0 0 12 12"><path d="M3 0h6v3H3zM1 4h10v5H9v3H3V9H1zm3 4v3h4V8z"/></svg>
            00.00.00.0000
          </span>
        </li>
        <li>
          <svg viewBox="0 0 12 12"><path d="M0 2h12v8H0zm1 1v.4l5 3.3 5-3.3V3zm0 1.6V9h10V4.6L6 7.9z"/></svg>
          yourname@yourwebsite.com
        </li>
        <li>
          <svg viewBox="0 0 12 12"><path d="M6 0a6 6 0 1 0 0 12A6 6 0 0 0 6 0zm0 1c.8 0 1.6 1.6 1.8 4H4.2C4.4 2.6 5.2 1 6 1zM1 6.5h2.2c.1 1.6.4 3 1 3.9A5 5 0 0 1 1 6.5zm0-1a5 5 0 0 1 3.2-3.9c-.6.9-.9 2.300-1 3.9zm5 5.5c-.8 0-1.6-1.6-1.8-4.5h3.6C7.6 9.4 6.8 11 6 11zm1.8-.6c.6-.9.9-2.3 1-3.9H11a5 5 0 0 1-3.2 3.9zM8.8 5.5c-.1-1.6-.4-3-1-3.9A5 5 0 0 1 11 5.5z"/></svg>
          www.yourwebsite.com
        </li>
      </ul>
    </div>
    <div class="silver-band"></div>
  </section>
</main>
</body>
</html>
```